Corvane Capital Business Cards

These are professional business cards that are for my family office.
Put fake emails and phone numbers as of now until I finalize those components. This family office controls my families investments, assets, and future. The cards should be professional.
..
.
.
.
I just uploaded another variation of a logo I would like to see as a business card to I am inbeteen which logo to use

Target Market(s)

business

Industry/Entity Type

business

Contact Information for Business Card

Professional, wealth related, finance related.

Requirements
Must have
• Logo

```html
<!DOCTYPE html>
<html lang="en">
<head>
<meta charset="utf-8">
<title>Corvane Capital Business Cards</title>
<link rel="stylesheet" href="https://fonts.googleapis.com/css2?family=Cinzel:wght@600&family=Montserrat:wght@400;700&display=swap">
<style>
  :root {
    --backdrop: #3a3a3c;
    --card: #f1f1f1;
    --ink: #141826;
    --ink-soft: #23283a;
  }
  * { margin: 0; padding: 0; box-sizing: border-box; }
  html, body { width: 1200px; height: 1059px; overflow: hidden; }
  body { background: var(--backdrop); position: relative; font-family: "Montserrat", sans-serif; color: var(--ink); }

  .card {
    position: absolute;
    background: var(--card);
    border-radius: 21px;
    overflow: hidden;
  }
  .card--front { left: 256px; top: 100px; width: 688px; height: 393px; }
  .card--back  { left: 253px; top: 536px; width: 694px; height: 396px; }

  .brand-name {
    position: absolute;
    font-family: "Cinzel", serif;
    font-weight: 600;
    color: var(--ink);
    white-space: nowrap;
    line-height: 1;
  }
  .card--front .brand-name--header { left: 29px; top: 44px; font-size: 33px; letter-spacing: 0.5px; }
  .card--front .brand-mark { position: absolute; left: 529px; top: 28px; }
  .card--front .brand-name--corner { right: 25px; top: 145px; font-size: 19px; }

  .accent-bar { position: absolute; left: 0; top: 200px; width: 20px; height: 56px; background: var(--ink); }
  .person-name { position: absolute; left: 29px; top: 197px; font-size: 30px; font-weight: 700; letter-spacing: 0.5px; }
  .person-title { position: absolute; left: 29px; top: 235px; font-size: 18px; color: var(--ink-soft); }
  .divider { position: absolute; left: 29px; top: 274px; width: 634px; height: 2px; background: var(--ink); }

  .contact-list { position: absolute; left: 29px; top: 292px; list-style: none; }
  .contact-list li { display: flex; align-items: center; height: 27px; font-size: 18px; color: var(--ink-soft); }
  .contact-list svg { width: 14px; height: 14px; margin-right: 9px; fill: var(--ink); }

  .address { position: absolute; right: 25px; top: 321px; text-align: right; font-size: 18px; line-height: 27px; color: var(--ink-soft); }

  .card--back .brand-mark { position: absolute; left: 272px; top: 88px; }
  .card--back .brand-name--center { left: 0; right: 0; top: 306px; text-align: center; font-size: 31px; letter-spacing: 0.5px; }
</style>
</head>
<body>
  <section class="card card--front">
    <div class="brand-name brand-name--header">Corvane Capital</div>
    <svg class="brand-mark" width="84" height="84" viewBox="0 0 84 84" aria-hidden="true">
      <circle cx="42" cy="42" r="39" fill="none" stroke="var(--ink)" stroke-width="3"/>
    </svg>
    <div class="brand-name brand-name--corner">Corvane Capital</div>

    <div class="accent-bar"></div>
    <div class="person-name">DANIEL HARTLEY</div>
    <div class="person-title">Managing Director</div>
    <div class="divider"></div>

    <ul class="contact-list">
      <li><svg viewBox="0 0 16 16"><path d="M2 6c0-2 3-3 6-3s6 1 6 3v1h-3V6H5v1H2zM4 8h8l2 5H2z"/></svg>555 010 4827</li>
      <li><svg viewBox="0 0 16 16"><path d="M1 3h14v2L8 9 1 5zM1 7l7 4 7-4v6H1z"/></svg>info@corvanecapital.com</li>
      <li><svg viewBox="0 0 16 16"><circle cx="8" cy="8" r="7"/><path d="M4 5h3v3H5zM9 9h3l-1 3H9z" fill="var(--card)"/></svg>www.corvanecapital.com</li>
    </ul>

    <div class="address">Your address, City<br>State, Zip 1234</div>
  </section>

  <section class="card card--back">
    <svg class="brand-mark" width="150" height="150" viewBox="0 0 150 150" aria-hidden="true">
      <circle cx="75" cy="75" r="71" fill="none" stroke="var(--ink)" stroke-width="4"/>
    </svg>
    <div class="brand-name brand-name--center">Corvane Capital</div>
  </section>
</body>
</html>
```